Healthcare website

We want to replace our website using joomla as the CMS. We want it to be device agnostic (gantry etc). Our business is health care our clients are people with high level spinal cord injuries ( quadriplegia / tetraplegia etc ). The site is a marketing tool primarily to potential clients and a portal for existing staff to access forms etc. It will showcase our key staff and our capability. It will also be where any new recruits apply to work with us. It must allow us to integrate our social media initiatives also. The final design must convey sophistication, high quality care and be warm and welcoming.

current web site is www.tendralwick.com.au
Updates

I have made small change to the brief in that i have removed the prefered color and indicated it would be nice to see some images that symbolize change / transformation like butterflies etc. thank you

Target Market(s)

Our business is health care our clients are people with high level spinal cord injuries ( quadriplegia / tetraplegia etc ).

Industry/Entity Type

Marketing

Colors

Designer to choose colors to be used in the design.

Requirements
Must have
• The site is a marketing tool primarily to potential clients and a portal for existing staff to access forms etc. It will showcase our key staff and our capability. It will also be where any new recruits apply to work with us. It must allow us to integrate our social media initiatives also. The final design must convey sophistication, high quality care and be warm and welcoming.
Nice to have
• Would be nice to incorporate images that symbolize change and new transformations - butterflies etc.

```html
<!DOCTYPE html>
<html lang="en">
<head>
<meta charset="utf-8">
<title>Tendralwick Care</title>
<link href="https://fonts.googleapis.com/css2?family=Nunito+Sans:wght@300;400;600&display=swap" rel="stylesheet">
<style>
:root{
  --blue:#2f74b8;
  --blue-dark:#2a68a6;
  --heading:#2e74b5;
  --text:#555;
  --dark:#333;
  --line:#dcdcdc;
  --grey-band:#e9e9e9;
  --card-bg:#f4f4f4;
  --white:#fff;
}
*{box-sizing:border-box;margin:0;padding:0}
html,body{width:808px;height:1200px;overflow:hidden;background:var(--white)}
body{position:relative;font-family:"Nunito Sans",Arial,sans-serif;color:var(--text);font-weight:300}
.abs{position:absolute}
.top-bar{left:0;top:0;width:808px;height:4px;background:var(--blue)}
.brand{left:50px;top:30px;display:flex;align-items:center;gap:6px;font-size:22px;font-weight:600;color:var(--blue)}
.brand-dot{width:22px;height:22px;border-radius:50%;background:var(--blue)}
.follow{left:600px;top:14px;display:flex;align-items:center;gap:4px;font-size:8.5px;color:var(--dark);font-weight:400}
.follow span{margin-right:4px}
.soc{width:19px;height:19px;border-radius:50%;background:#a9a9a9;display:inline-block}
.nav{left:400px;top:55px;display:flex;font-size:8.5px;font-weight:400;color:var(--blue);text-transform:uppercase}
.nav a{display:block;height:24px;line-height:24px;text-decoration:none;color:var(--blue);margin-right:26px;white-space:nowrap}
.nav a.active{background:var(--blue);color:#fff;padding:0 16px;margin-right:15px}
.nav a:last-child{margin-right:0}
.hero{left:50px;top:87px;width:708px;height:240px;border:1px solid var(--line);padding:3px;background:#fff}
.hero-img{width:100%;height:100%;background:linear-gradient(90deg,#b9b9b6 0%,#d6d3cf 35%,#e9eef2 65%,#f2f5f8 100%)}
.hero-copy{right:24px;top:70px;text-align:right;color:var(--dark)}
.hero-copy h1{font-size:33px;font-weight:400;color:var(--heading);line-height:1.1}
.hero-copy p{font-size:16px;font-weight:400;line-height:21px}
.dots{left:326px;top:213px;display:flex;gap:5px}
.dots i{width:10px;height:10px;border-radius:50%;background:#111;display:block}
.dots i:first-child{background:var(--blue)}
.welcome{left:50px;top:353px;width:708px;text-align:center}
.welcome h2{font-size:16px;font-weight:400;color:var(--heading);display:flex;align-items:center;gap:26px}
.welcome h2::before,.welcome h2::after{content:"";flex:1;height:1px;background:var(--line)}
.welcome p{margin-top:12px;font-size:8.7px;line-height:14.4px;color:var(--dark)}
.btn{display:block;background:var(--blue);color:#fff;font-size:8.8px;font-weight:400;text-align:center;text-transform:uppercase}
.welcome-btn{left:360px;top:469px;width:87px;height:26px;line-height:26px}
.rule{left:50px;width:708px;height:1px;background:var(--line)}
h3.sec{position:absolute;font-size:16px;font-weight:400;color:var(--heading)}
.service{top:561px;width:163px}
.service .ph{height:95px}
.service p{margin-top:8px;font-size:11.5px;color:var(--dark);font-weight:400}
.join{left:595px;top:534px;width:163px;height:142px;background:var(--blue);color:#fff;text-align:center;padding:10px 14px}
.join h4{font-size:15px;font-weight:400}
.join p{margin-top:6px;font-size:8.2px;line-height:14.4px}
.join .btn{margin:10px auto 0;width:86px;height:23px;line-height:23px;background:#f5f5f5;color:var(--dark)}
.news{left:50px;top:754px;width:220px;list-style:none;font-size:8.5px;line-height:13px;color:var(--dark)}
.news li{position:relative;padding-left:15px;margin-bottom:11px}
.news li::before{content:"›";position:absolute;left:0;top:-1px;color:var(--blue);font-weight:600;font-size:11px}
.news-btn{left:50px;top:909px;width:88px;height:26px;line-height:26px}
.divider{left:283px;top:724px;width:1px;height:212px;background:var(--line)}
.arrows{left:736px;top:723px;color:var(--blue);font-size:16px;letter-spacing:6px}
.member{top:752px;width:142px;height:182px;border:1px solid #e6e6e6;background:#fff}
.member .ph{margin:10px auto 0;width:117px;height:111px;border:1px solid #eee;background:linear-gradient(180deg,#f3f3f3 0%,#d9d9d9 100%)}
.member .name{margin-top:7px;text-align:center;font-size:9.5px;color:var(--dark);font-weight:400}
.member .bar{position:absolute;left:0;bottom:0;width:100%;height:32px;background:#e4e4e4;display:flex;justify-content:center;align-items:center;gap:4px}
.member .bar i{width:19px;height:19px;border-radius:50%;background:var(--blue);display:block}
.band{left:0;top:958px;width:808px;height:173px;background:var(--grey-band)}
.licensed{left:50px;top:1000px;width:215px;font-size:8.5px;line-height:15px}
.contact{left:319px;top:1000px;font-size:8.5px;line-height:15px}
.contact strong{font-weight:600;color:var(--dark)}
.contact a{color:var(--blue);text-decoration:none}
.map{left:456px;top:976px;width:302px;height:138px;border:2px solid #c9c9c9;background:linear-gradient(135deg,#eeece6 0%,#e4e1d8 100%)}
.footer{left:0;top:1131px;width:808px;height:69px;background:var(--blue);color:#fff;font-size:8.5px;line-height:17px}
.footer .copy{position:absolute;left:50px;top:17px}
.badges{position:absolute;right:50px;top:22px;display:flex;gap:14px;align-items:center}
.badges i{display:block;background:rgba(255,255,255,.75);border-radius:3px}
</style>
</head>
<body>
<div class="abs top-bar"></div>

<div class="abs brand"><span>tendralwick</span><span class="brand-dot"></span></div>

<div class="abs follow"><span>Follow Us:</span><i class="soc"></i><i class="soc"></i><i class="soc"></i><i class="soc"></i><i class="soc"></i></div>

<nav class="abs nav">
  <a class="active">Home</a><a>About Us</a><a>Our Services</a><a>Resources</a><a>Contact Us</a>
</nav>

<section class="abs hero">
  <div class="hero-img" role="img" aria-label="Physiotherapist guiding a young woman through a rehabilitation exercise in a gym"></div>
  <div class="abs hero-copy">
    <h1>Tendralwick Care</h1>
    <p>Spinal Cord &amp; ABI in Home Specialised Care</p>
    <p>Attendant Care</p>
  </div>
  <div class="abs dots"><i></i><i></i><i></i><i></i></div>
</section>

<section class="abs welcome">
  <h2>Welcome to Our Website</h2>
  <p>Tendralwick Care is a small team of care professionals committed to providing quality one-to-one care with heart.<br>
  Tendralwick Care has built its service around the needs of each and every client. We listen to and consult with our clients, their families, Care Teams and the wider care community. Tendralwick Care is a privately owned organisation providing in home care for people with disabilities (attendant care) throughout the State of Victoria. We commenced operation on the 1st of July 2004 at our principal office in Elmsbrook, Victoria.</p>
</section>
<a class="abs btn welcome-btn">Read More</a>

<div class="abs rule" style="top:517px"></div>

<h3 class="sec" style="left:50px;top:530px">Our Services</h3>
<div class="abs service" style="left:50px"><div class="ph" role="img" aria-label="Therapist examining a patient's shoulder" style="background:linear-gradient(135deg,#cfc3b3,#a9886c)"></div><p>Spinal Care &nbsp;»</p></div>
<div class="abs service" style="left:232px"><div class="ph" role="img" aria-label="Wheelchair wheel against a blue sky" style="background:linear-gradient(180deg,#2d5f9c,#8fb3d9 60%,#6a6a6a)"></div><p>Quadriplegia &nbsp;»</p></div>
<div class="abs service" style="left:414px"><div class="ph" role="img" aria-label="Carer with an older man in a wheelchair in a garden" style="background:linear-gradient(180deg,#8fae5c,#5f8a36)"></div><p>Tetraplegia &nbsp;»</p></div>

<aside class="abs join">
  <h4>Join Our Team</h4>
  <p>We are always on the lookout for great people to work with our clients. If you want to be a part of our Team click below to apply.</p>
  <a class="btn">Join Now</a>
</aside>

<div class="abs rule" style="top:706px"></div>

<h3 class="sec" style="left:50px;top:720px">Disability News</h3>
<ul class="abs news">
  <li>New Methods Show Promise for Rehabilitating Paralyzed Patients With Spinal Cord Injury..</li>
  <li>Stem-cell advances may quell ethics debate</li>
  <li>Wheelchair rugby a family affair for mom and son</li>
  <li>Stem Cells Fast Facts</li>
  <li>Attitude can play significant role in recovery from paralyzing injury..</li>
</ul>
<a class="abs btn news-btn">Read More</a>

<div class="abs divider"></div>

<h3 class="sec" style="left:302px;top:720px">Our Team</h3>
<div class="abs arrows">‹›</div>

<div class="abs member" style="left:302px"><div class="ph" role="img" aria-label="Portrait of team member"></div><p class="name">Helena Marwick</p><div class="bar"><i></i><i></i><i></i><i></i></div></div>
<div class="abs member" style="left:460px"><div class="ph" role="img" aria-label="Portrait of team member"></div><p class="name">Helena Marwick</p><div class="bar"><i></i><i></i><i></i><i></i></div></div>
<div class="abs member" style="left:618px"><div class="ph" role="img" aria-label="Portrait of team member"></div><p class="name">Helena Marwick</p><div class="bar"><i></i><i></i><i></i><i></i></div></div>

<div class="abs band"></div>
<h3 class="sec" style="left:50px;top:972px">Licensed</h3>
<p class="abs licensed">Tendralwick Care is proud to be an approved provider for Road Injury Commission (RIC), State Worksafe Authority (SWA), Department of Community Services (DCS) and maintain associations and cooperative relationships with a variety of private and governmental organisations in its efforts to bring the finest, most up-to-date care for its clients.</p>

<h3 class="sec" style="left:319px;top:972px">Contact Info</h3>
<p class="abs contact"><strong>Tendralwick Care – Melbourne</strong><br>42 – 46 Larkspur Rd<br>Elmsbrook<br>Victoria, 3188<br><strong>Ph:</strong> <a>(03) 9000 4812</a></p>

<div class="abs map" role="img" aria-label="Street map showing the office location"></div>

<footer class="abs footer">
  <p class="copy">© 2004 - 2014 Tendralwick Care Pty Ltd<br>All Right Reserved</p>
  <div class="badges">
    <i style="width:18px;height:24px"></i><i style="width:14px;height:22px"></i><i style="width:32px;height:14px"></i><i style="width:58px;height:16px"></i><i style="width:40px;height:26px"></i><i style="width:26px;height:14px"></i><i style="width:16px;height:24px"></i>
  </div>
</footer>
</body>
</html>
```